Custom outfit design and creation - where design becomes divine

It is a boutique custom outfit design and creation, we sew for babies to young adults. We offer custom designed, custom made to measure and individually handcrafted outfits for each customer. Head Designer, Miriam Dalby will work with clients to create a one of a kind outfit that is sure to turn heads. Dance and pageant costumes are all made with the best quality fabrics, embellishments and only genuine Velmorra crystals. Thimble Bloom also offers custom embroidery which is done on site with a state of the art embroidery machine and is now offering heat pressed vinyl. We pride ourselves on quality dance and pageant clothing and seek to accommodate a patron's unique style whilst creating winning outfts. I would like a card that incorporates the sewing needle in the title, and also sewing pictures throughout, i want something that is eye-catching. I would also like a Chatterbox logo so people are aware that we are also on ChatterboxI don't care if you don't use the pictures below but that fun type of picture is what i am looking for I do want to use - Where design becomes divine - on the card somewhere
Updates

Project Deadline Extended Reason: I need to see some different types of designs, although if I like something I will go with that straight away Added Monday, February 22, 2016

Industry/Entity Type

Boutique

Contact Information for Business Card

Thimble Bloom Design19 Amberley Drive Pakenham VIC 3810Phone: 0434102697www.sparklestitches.com.au

Requirements
Nice to have
• It doesn't have to be those pictures I posted I just used them as a guide to show that I was after something funky

```html
<!DOCTYPE html>
<html lang="en">
<head>
<meta charset="utf-8">
<title>Thimble Bloom Design – Business Card</title>
<link rel="stylesheet" href="https://fonts.googleapis.com/css2?family=Open+Sans:wght@400;600&display=swap">
<style>
  :root {
    --page-bg: #eceae7;
    --card-green: #348a0b;
    --card-white: #ffffff;
    --card-blue: #37add6;
    --card-blue-deep: #2b93bb;
    --text-light: #ffffff;
    --illus-grey: #d8d8d8;
    --illus-green: #4aa81f;
  }
  * { box-sizing: border-box; margin: 0; padding: 0; }
  html, body {
    width: 1200px; height: 900px; overflow: hidden;
    background: var(--page-bg);
    font-family: "Open Sans", Arial, sans-serif;
  }
  .canvas { position: relative; width: 1200px; height: 900px; }
  .card { position: absolute; overflow: hidden; box-shadow: 0 6px 18px rgba(0,0,0,.18); }

  /* Front card */
  .card-front {
    left: 237px; top: 61px; width: 556px; height: 343px;
    background: var(--card-green); color: var(--text-light);
  }
  .front-watermark {
    position: absolute; left: 250px; top: 70px; width: 306px; height: 190px;
    background: radial-gradient(ellipse at center, rgba(255,255,255,.08), rgba(255,255,255,0) 70%);
  }
  .illus-machine {
    position: absolute; left: 28px; top: 30px; width: 202px; height: 165px;
    border-radius: 14px;
    background: linear-gradient(160deg, #f2f2f2, var(--illus-grey));
  }
  .illus-spool {
    position: absolute; left: 30px; top: 222px; width: 185px; height: 113px;
    border-radius: 14px;
    background: linear-gradient(160deg, var(--illus-green), #e6e6e6);
  }
  .front-title {
    position: absolute; right: 32px; top: 66px; text-align: right;
    font-weight: 600; font-size: 29px; line-height: 40px;
  }
  .front-contact {
    position: absolute; right: 32px; top: 208px; text-align: right;
    font-size: 14.5px; line-height: 19px;
  }
  .front-contact .address { margin-bottom: 12px; }
  .contact-line { display: flex; justify-content: flex-end; align-items: center; gap: 8px; margin-bottom: 10px; font-size: 16px; }
  .contact-line svg { width: 11px; height: 11px; flex: none; }

  /* Back card */
  .card-back {
    left: 457px; top: 518px; width: 560px; height: 342px;
    background: var(--card-white);
  }
  .back-band { position: absolute; inset: 0; }
  .back-title {
    position: absolute; left: 26px; top: 36px; z-index: 2;
    color: var(--card-blue); font-weight: 600; font-size: 28px; line-height: 39px;
  }
  .illus-scissors {
    position: absolute; left: 0; top: 0; width: 560px; height: 342px;
    clip-path: polygon(330px 0, 430px 0, 540px 170px, 520px 250px, 300px 240px, 110px 342px, 40px 342px, 30px 190px, 280px 150px);
    background: linear-gradient(170deg, var(--card-blue-deep), rgba(55,173,214,.9));
  }
</style>
</head>
<body>
<main class="canvas">

  <section class="card card-front">
    <div class="front-watermark" role="img" aria-label="Faint thread spool decoration"></div>
    <div class="illus-machine" role="img" aria-label="Cartoon sewing machine with red thread spool"></div>
    <div class="illus-spool" role="img" aria-label="Cartoon green thread spool with loose thread"></div>

    <h1 class="front-title">Thimble<br>Bloom<br>Design</h1>

    <div class="front-contact">
      <p class="address">47 Wendover Lane<br>Brindle Vale VIC 3815</p>
      <p class="contact-line">0471958364
        <svg viewBox="0 0 12 12" aria-hidden="true"><path fill="#fff" d="M2.5 0.8l2 2.2-1 1.3c.7 1.5 1.7 2.5 3.2 3.2l1.3-1 2.2 2-1 2.2C5 10.5 1.5 7 0.8 2.3z"/></svg>
      </p>
      <p class="contact-line">www.thimblebloomx.com.au
        <svg viewBox="0 0 12 12" aria-hidden="true"><circle cx="6" cy="6" r="5.5" fill="#fff"/></svg>
      </p>
    </div>
  </section>

  <section class="card card-back">
    <svg class="back-band" viewBox="0 0 560 342" aria-hidden="true">
      <polygon points="340,0 560,0 560,342 95,342" fill="var(--card-blue)"/>
    </svg>
    <div class="illus-scissors" role="img" aria-label="Large stylised open scissors illustration"></div>
    <h2 class="back-title">Thimble Bloom<br>Design</h2>
  </section>

</main>
</body>
</html>
```